Modern, clean and professional Wordpress design for a safety training company!

We are currently in the process of creating a new website for our business. We have hired a website developer and the main structure of our new Wordpress site is complete. We now need an overall design plan for the site. We need a very clean, professional and easy to follow website. Most of our website visitors only spend about 30-45 secs on our sites "shopping " so it is imperative that we have a strong Home Page.
Our company specializes in CPR and First Aid Certification Classes to businesses and individuals throughout Northern California. We provide these certifications two ways: ONSITE-We come to you, and HOSTED-we offer weekly classes at our 2 locations.
Our design needs to use the general green and blue colors of our logo. But we also like white.
The final design MUST communicate a legitimate, trustworthy and professional business. Our industry is VERY competitive and we need to STAND OUT.
Currently, the NEW website that we need a new design for is www.LifelineDrillWorks.com
Our old website is www.RescuePrepValleyHub.com and we really do like the design of this website, but we just needed a Wordpress site for SEO purposes.
These are 3 websites that we really:
http://morvaliontech.com/
http://www.tralbex.com/
https://www.plivant.com/
I have attached our Logo and other images if you need to use them but looking at the current two sites will be you best help.
Target Market(s)
1) Large businesses and industries that are looking for a company to provide ONSITE safety training classes at their office or place of work.
2) Individuals that need certifications for their jobs and other needs. These individuals are looking for a legitimate, trustworthy and professional environment to complete their training class.

```html
<!DOCTYPE html>
<html lang="en">
<head>
<meta charset="utf-8">
<title>Keystone Safety Academy — CPR &amp; First Aid Training</title>
<link rel="stylesheet" href="https://fonts.googleapis.com/css2?family=Noto+Serif:wght@400&family=Open+Sans:wght@400;600&display=swap">
<style>
  :root {
    --navy: #17246e;
    --navy-deep: #0d1a5c;
    --blue-top: #1f3c8f;
    --green: #8dba12;
    --green-top: #a3c80f;
    --green-logo: #6f9e1a;
    --ink: #4a4a4a;
    --muted: #8a8a8a;
    --dark-top: #3a3a3a;
    --dark-bottom: #1f1f1f;
    --band: #efefef;
    --footer: #272727;
    --white: #ffffff;
    --star: #f5c400;
  }
  * { box-sizing: border-box; margin: 0; padding: 0; }
  html, body { width: 1162px; height: 1200px; overflow: hidden; background: var(--white); }
  body { position: relative; font-family: "Open Sans", sans-serif; color: var(--ink); }
  .abs { position: absolute; }

  /* Header */
  .brand { left: 96px; top: 48px; display: flex; align-items: center; gap: 10px; }
  .brand-dot { width: 34px; height: 34px; border-radius: 50%; background: var(--green-logo); }
  .brand-name { font-weight: 600; font-size: 22px; line-height: 1.1; color: var(--navy); width: 200px; }
  .contact-top { right: 135px; top: 23px; text-align: right; white-space: nowrap; }
  .contact-top .email { font-size: 12.5px; line-height: 17px; color: #555; }
  .contact-top .phone { font-size: 20px; line-height: 26px; color: var(--navy); letter-spacing: .3px; }
  .phone-badge { left: 1033px; top: 31px; width: 32px; height: 32px; border-radius: 50%; background: #5a5a5a; display: flex; align-items: center; justify-content: center; }
  .main-nav { right: 98px; top: 103px; display: flex; gap: 32px; font-size: 13px; color: var(--muted); white-space: nowrap; }
  .main-nav .current { color: var(--navy); }

  /* Hero */
  .hero { left: 0; top: 142px; width: 1162px; height: 495px;
    background: linear-gradient(180deg, #e6e9ec 0%, #cfc8bd 45%, #7b6a5c 80%, #5b4d45 100%); }
  .slide-arrow { top: 376px; width: 29px; height: 29px; background: rgba(90,90,90,.8); display: flex; align-items: center; justify-content: center; }
  .slide-arrow.prev { left: 0; }
  .slide-arrow.next { right: 0; background: rgba(255,255,255,.25); }

  /* Feature panels */
  .welcome { left: 108px; top: 548px; width: 299px; height: 315px; background: linear-gradient(180deg, #efefef, #e6e6e6); padding: 24px 20px 0 22px; }
  .welcome h1 { font-family: "Noto Serif", serif; font-weight: 400; font-size: 29px; color: var(--navy); line-height: 1.1; }
  .welcome h2 { font-family: "Noto Serif", serif; font-weight: 400; font-size: 16.5px; color: var(--navy); margin-top: 2px; white-space: nowrap; }
  .welcome p { font-size: 11.6px; line-height: 21.6px; color: #555; margin-top: 10px; }
  .btn-light { display: inline-block; margin-top: 22px; background: var(--white); color: #666; font-size: 10.5px; padding: 9px 13px; letter-spacing: .2px; }

  .offer { left: 407px; width: 299px; height: 158px; color: var(--white); padding: 14px 16px 0 16px; }
  .offer.cpr { top: 548px; background: linear-gradient(180deg, var(--green-top), #7faa10); }
  .offer.bls { top: 706px; height: 157px; background: linear-gradient(180deg, var(--blue-top), var(--navy-deep)); }
  .offer .title { font-family: "Noto Serif", serif; font-size: 56px; line-height: 1; display: flex; align-items: baseline; gap: 18px; }
  .offer .price { font-size: 38px; }
  .offer ul { list-style: none; font-family: "Noto Serif", serif; font-size: 12.5px; margin-top: 12px; }
  .offer li { line-height: 24px; padding-left: 13px; position: relative; white-space: nowrap; }
  .offer li::before { content: "•"; position: absolute; left: 1px; }
  .btn-register { position: absolute; left: 163px; top: 87px; width: 124px; height: 40px; background: var(--white); color: #6c6c6c; font-size: 12.5px; display: flex; align-items: center; justify-content: center; letter-spacing: .4px; }
  .offer.bls .btn-register { top: 88px; }

  .reviews { left: 706px; top: 548px; width: 348px; height: 315px; background: linear-gradient(180deg, var(--dark-top), var(--dark-bottom)); padding: 33px 30px 0 30px; color: #d8d8d8; }
  .reviews h3 { font-family: "Noto Serif", serif; font-weight: 400; font-size: 16px; color: #e6e6e6; letter-spacing: .4px; }
  .review-meta { font-family: "Noto Serif", serif; font-size: 11.6px; line-height: 18px; margin-top: 36px; color: #dcdcdc; }
  .stars { margin-top: 4px; display: flex; gap: 2px; }
  .review-text { font-size: 10.4px; line-height: 18.2px; color: #9c9c9c; margin-top: 6px; }
  .review-badge { margin-top: 34px; width: 80px; height: 20px; border-radius: 3px; background: #4c4c4c; }

  /* Info band */
  .info-band { left: 0; top: 908px; width: 1162px; height: 194px; background: var(--band); }
  .info-col h4 { font-size: 15px; font-weight: 600; color: #5a5a5a; letter-spacing: .2px; white-space: nowrap; }
  .col-social { left: 111px; top: 935px; width: 290px; }
  .col-contact { left: 477px; top: 935px; }
  .col-map { left: 757px; top: 935px; }
  .divider { top: 932px; width: 1px; height: 142px; background: #cfcfcf; }
  .like-box { left: 340px; top: 936px; display: flex; gap: 4px; font-size: 9px; }
  .like-box span { border: 1px solid #c8c8c8; background: #fff; padding: 1px 4px; color: #3b5998; }
  .like-box span + span { color: #444; }
  .post-card { left: 111px; top: 965px; width: 291px; height: 109px; background: var(--white); padding: 10px 12px; display: flex; gap: 10px; }
  .post-avatar { width: 33px; height: 31px; background: linear-gradient(135deg, #c9a58a, #4a3f48); flex: none; }
  .post-card .who { font-size: 11px; font-weight: 600; color: var(--navy); }
  .post-card .msg { font-size: 9.6px; line-height: 15px; color: #555; margin-top: 4px; }
  .post-card .actions { font-size: 8.8px; color: var(--navy); margin-top: 10px; }
  .contact-list { list-style: none; margin-top: 14px; font-size: 12px; color: #6a6a6a; }
  .contact-list li { display: flex; gap: 14px; margin-bottom: 13px; line-height: 18px; white-space: nowrap; }
  .contact-list .ic { width: 12px; flex: none; display: flex; justify-content: center; padding-top: 3px; }
  .contact-list .big { font-size: 13.8px; }
  .map { left: 757px; top: 965px; width: 295px; height: 107px; border: 3px solid #fff;
    background: linear-gradient(135deg, #e4e0d6, #d8d4ca); }

  /* Footer */
  .site-footer { left: 0; top: 1102px; width: 1162px; height: 98px; background: var(--footer); }
  .footer-nav { left: 96px; top: 1124px; font-size: 11.2px; color: #c8c8c8; display: flex; gap: 10px; white-space: nowrap; }
  .footer-nav .sep { color: #666; }
  .copyright { left: 96px; top: 1152px; font-size: 11.2px; color: #c0c0c0; white-space: nowrap; }
  .social { left: 838px; top: 1133px; display: flex; gap: 6px; }
  .social span { width: 27px; height: 27px; border-radius: 50%; background: #5b5b5b; display: block; }
</style>
</head>
<body>

<header>
  <div class="abs brand">
    <span class="brand-dot"></span>
    <span class="brand-name">Keystone Safety<br>Academy</span>
  </div>
  <div class="abs contact-top">
    <div class="email">info@keystonecpr.com</div>
    <div class="phone">916-555-0182</div>
  </div>
  <div class="abs phone-badge">
    <svg width="13" height="13" viewBox="0 0 24 24"><path fill="#fff" d="M6.6 10.8a15.1 15.1 0 0 0 6.6 6.6l2.2-2.2c.3-.3.7-.4 1-.2 1.1.4 2.3.6 3.6.6.6 0 1 .4 1 1V20c0 .6-.4 1-1 1A17 17 0 0 1 3 4c0-.6.4-1 1-1h3.5c.6 0 1 .4 1 1 0 1.3.2 2.5.6 3.6.1.3 0 .7-.2 1z"/></svg>
  </div>
  <nav class="abs main-nav">
    <span class="current">Home</span>
    <span>Class Calender</span>
    <span>Classes for Groups</span>
    <span>Certification Classes</span>
    <span>About Us</span>
    <span>Policies</span>
  </nav>
</header>

<section class="abs hero" role="img" aria-label="Photo of adults seated in a bright classroom listening to an instructor"></section>
<div class="abs slide-arrow prev"><svg width="13" height="11" viewBox="0 0 13 11"><path d="M12 5.5H2M6 1 1.5 5.5 6 10" stroke="#fff" stroke-width="2.2" fill="none"/></svg></div>
<div class="abs slide-arrow next"><svg width="13" height="11" viewBox="0 0 13 11"><path d="M1 5.5h10M7 1l4.5 4.5L7 10" stroke="#ddd" stroke-width="2.2" fill="none"/></svg></div>

<section class="abs welcome">
  <h1>Welcome to</h1>
  <h2>Keystone Safety Academy!</h2>
  <p>Keystone Safety Academy is Northern California’s leader in CPR, BLS, and Basic First Aid Certifications! Taught by experienced Fire-fighters, our classes are much shorter and provide common sense knowledge and skills to each student to help prepare them for actual emergencies.</p>
  <span class="btn-light">READ MORE</span>
</section>

<section class="abs offer cpr">
  <div class="title">CPR <span class="price">- $39</span></div>
  <ul><li>Adult/Child/Infant</li><li>90 Minutes!</li></ul>
  <span class="btn-register">REGISTER NOW</span>
</section>
<section class="abs offer bls">
  <div class="title">BLS <span class="price">- $49</span></div>
  <ul><li>Healthcare/Dental</li><li>90 Minutes!</li></ul>
  <span class="btn-register">REGISTER NOW</span>
</section>

<section class="abs reviews">
  <h3>REVIEWS</h3>
  <div class="review-meta">Janelle - CA, United States<br>August 25, 2014</div>
  <div class="stars">
    <svg width="84" height="15" viewBox="0 0 84 15">
      <defs><path id="star" d="M7.5 0l2.2 4.7 5.1.6-3.8 3.5 1 5.1-4.5-2.6L3 13.9l1-5.1L.2 5.3l5.1-.6z"/></defs>
      <use href="#star" fill="var(--star)"/>
      <use href="#star" x="17" fill="var(--star)"/>
      <use href="#star" x="34" fill="var(--star)"/>
      <use href="#star" x="51" fill="var(--star)"/>
      <use href="#star" x="68" fill="var(--star)"/>
    </svg>
  </div>
  <p class="review-text">Very informative and encouraging class! I learned that it is important for everyone to know how and why to perform CPR and I am so glad that I was able to learn the material from a firefighter who actually does this for a living.</p>
  <div class="review-badge"></div>
</section>

<section class="abs info-band"></section>
<div class="abs divider" style="left:440px"></div>
<div class="abs divider" style="left:713px"></div>

<div class="abs info-col col-social"><h4>FIND US ON FRIENDWALL</h4></div>
<div class="abs like-box"><span>Like</span><span>3k</span></div>
<div class="abs post-card">
  <div class="post-avatar" role="img" aria-label="Small profile photo"></div>
  <div>
    <div class="who">Keystone Safety Academy</div>
    <div class="msg">Does your office or place of business need to be CPR or First Aid certified? Call KSA and we'll come to you!</div>
    <div class="actions">Like&nbsp; ::&nbsp; Comment</div>
  </div>
</div>

<div class="abs info-col col-contact">
  <h4>CONTACT US</h4>
  <ul class="contact-list">
    <li><span class="ic"><svg width="8" height="11" viewBox="0 0 8 11"><path d="M4 0a4 4 0 0 0-4 4c0 3 4 7 4 7s4-4 4-7a4 4 0 0 0-4-4zm0 5.5A1.5 1.5 0 1 1 4 2.5a1.5 1.5 0 0 1 0 3z" fill="#888"/></svg></span><span>Address: 2870 Alder Creek Rd #140<br>Rancho Cordova, CA 95670</span></li>
    <li class="big"><span class="ic"><svg width="11" height="11" viewBox="0 0 24 24"><path fill="#888" d="M6.6 10.8a15.1 15.1 0 0 0 6.6 6.6l2.2-2.2c.3-.3.7-.4 1-.2 1.1.4 2.3.6 3.6.6.6 0 1 .4 1 1V20c0 .6-.4 1-1 1A17 17 0 0 1 3 4c0-.6.4-1 1-1h3.5c.6 0 1 .4 1 1 0 1.3.2 2.5.6 3.6.1.3 0 .7-.2 1z"/></svg></span><span>Phone: 916-555-0182</span></li>
    <li class="big"><span class="ic"><svg width="11" height="9" viewBox="0 0 11 9"><rect width="11" height="9" rx="1" fill="#888"/><path d="M.5 1 5.5 5l5-4" stroke="#efefef" fill="none"/></svg></span><span>Email: info@keystonecpr.com</span></li>
  </ul>
</div>

<div class="abs info-col col-map"><h4>GET DIRECTIONS</h4></div>
<div class="abs map" role="img" aria-label="Street map showing the training center location"></div>

<footer class="abs site-footer"></footer>
<nav class="abs footer-nav">
  <span>Home</span><span class="sep">|</span><span>Class Calender</span><span class="sep">|</span><span>Classes for Groups</span><span class="sep">|</span><span>Certification Classes</span><span class="sep">|</span><span>About Us</span><span class="sep">|</span><span>Policies</span>
</nav>
<div class="abs copyright">Copyright &nbsp;©&nbsp; 2015 &nbsp;Keystone Safety Academy. All rights reserved.</div>
<div class="abs social" aria-label="Social links">
  <span></span><span></span><span></span><span></span><span></span><span></span><span></span>
</div>

</body>
</html>
```